Professional and creative business card design for recruiting service providers

Our company supports German medium-sized companies in filling vacancies promptly. For this we use social media marketing and bring our customers into the visibility.

We want a professional but also creative design for our business cards.

Please look at lindqvar-staff.de to get an impression of our CI.

Target Market(s)

Small and medium-sized companies in Germany from the industry

Industry/Entity Type

Industrie, Handwerk

Contact Information for Business Card

Name, Position, Telefonnummer, Email, Website

Colors
EE7325
F08F49
F5BC92
FAE3D3
FDF4ED

Requirements
Must have
• A picture of the employee and in the style of www.lindqvar-staff.de

```html
<!DOCTYPE html>
<html lang="en">
<head>
<meta charset="utf-8">
<title>Lindqvar &amp; Staff – Business Card</title>
<link href="https://fonts.googleapis.com/css2?family=Jost:wght@400;500;600&family=Montserrat:wght@700&display=swap" rel="stylesheet">
<style>
  :root {
    --orange: #ee6a2e;
    --black: #000000;
    --white: #ffffff;
    --stage: #d4d4d4;
    --photo-light: #e4e2e4;
    --photo-dark: #2a2c36;
  }
  * { box-sizing: border-box; margin: 0; padding: 0; }
  html, body {
    width: 1200px; height: 800px; overflow: hidden;
    background: var(--stage);
  }
  .stage { position: relative; width: 1200px; height: 800px; }
  .card {
    position: absolute; top: 240px;
    width: 560px; height: 320px;
    border-radius: 16px;
    overflow: hidden;
    box-shadow: 0 3px 0 var(--orange), 0 14px 30px rgba(0,0,0,0.22);
  }
  /* Front */
  .card--front { left: 25px; background: var(--white); }
  .front__block {
    position: absolute; left: 440px; top: 40px;
    width: 120px; height: 72px; background: var(--black);
  }
  .front__identity {
    position: absolute; left: 34px; top: 80px;
    width: 270px;
    font-family: "Jost", sans-serif;
  }
  .front__name {
    font-size: 21px; font-weight: 600; letter-spacing: 0.4px;
    color: var(--black); line-height: 1.05; white-space: nowrap;
  }
  .front__role {
    font-size: 15px; font-weight: 400; letter-spacing: 0.4px;
    color: var(--orange); text-transform: uppercase; margin-top: 2px;
  }
  .front__band {
    position: absolute; left: 0; top: 150px;
    width: 320px; height: 100px; background: var(--orange);
    padding: 14px 0 0 34px;
  }
  .contact {
    list-style: none;
    font-family: "Jost", sans-serif; font-size: 16px; font-weight: 500;
    color: var(--white); line-height: 24px;
  }
  .contact li { display: flex; align-items: center; gap: 8px; white-space: nowrap; }
  .contact svg { width: 14px; height: 14px; flex: none; }
  .front__photo {
    position: absolute; left: 320px; top: 72px;
    width: 200px; height: 200px;
    border: 2px solid var(--orange);
    background: linear-gradient(160deg, var(--photo-light) 0%, var(--photo-light) 45%, var(--photo-dark) 100%);
  }
  /* Back */
  .card--back {
    left: 615px; background: var(--black);
    display: flex; align-items: center; justify-content: center; gap: 22px;
  }
  .brand__mark { width: 64px; height: 64px; background: var(--orange); }
  .brand__name {
    font-family: "Montserrat", sans-serif; font-weight: 700;
    font-size: 30px; line-height: 1.05; letter-spacing: 2px;
    color: var(--white); text-transform: uppercase;
  }
</style>
</head>
<body>
<main class="stage">
  <section class="card card--front">
    <div class="front__block"></div>
    <div class="front__identity">
      <p class="front__name">JONAS HALVERMANN</p>
      <p class="front__role">Managing Director</p>
    </div>
    <div class="front__band">
      <ul class="contact">
        <li>
          <svg viewBox="0 0 16 16"><path fill="#fff" d="M3.6 1.5l2.3 2.6-1.3 1.6c.9 2 2.6 3.6 4.6 4.6l1.6-1.3 2.6 2.3-1.3 2.4C6.7 13.6 2.4 9.3 1.5 3.1z"/></svg>
          0421-987 654 32
        </li>
        <li>
          <svg viewBox="0 0 16 16"><rect x="1" y="3" width="14" height="10" fill="none" stroke="#fff" stroke-width="1.6"/><path d="M1 3l7 6 7-6" fill="none" stroke="#fff" stroke-width="1.6"/></svg>
          info@lindqvar-staff.de
        </li>
        <li>
          <svg viewBox="0 0 16 16"><circle cx="8" cy="8" r="6.5" fill="none" stroke="#fff" stroke-width="1.5"/><path d="M1.5 8h13M8 1.5c-3 3.5-3 9.5 0 13M8 1.5c3 3.5 3 9.5 0 13" fill="none" stroke="#fff" stroke-width="1.2"/></svg>
          www.lindqvar-staff.de
        </li>
      </ul>
    </div>
    <div class="front__photo" role="img" aria-label="Portrait photo of the employee"></div>
  </section>

  <section class="card card--back">
    <div class="brand__mark"></div>
    <p class="brand__name">Lindqvar<br>&amp; Staff</p>
  </section>
</main>
</body>
</html>
```